Business Card for Coastal Tundrabridge Advisory

We need a business card for Coastal Tundrabridge Advisory. The company website address is provided below. The company logo is attached. We provide specialized permafrost services to the mining, transportation, and oil & gas industries. The card should be prepared for:
Matthias Korhonen, PhD.
Coastal Tundrabridge Advisory
PO Box 418259
Quillwater, Alaska 99642
Direct: +1-907-555-0143
Email: mkorhonen@tundrabridgeadvisory.example
Website: www.coastaltundrabridgeadvisory.example

```html
<!DOCTYPE html>
<html lang="en">
<head>
<meta charset="utf-8">
<title>Coastal Tundrabridge Advisory – Business Card</title>
<link rel="stylesheet" href="https://fonts.googleapis.com/css2?family=Montserrat:wght@300;600&family=Roboto:wght@400;700&display=swap">
<style>
  :root {
    --stage: #222222;
    --card: #111722;
    --ink: #ffffff;
    --ink-soft: #e6e8ec;
  }
  * { box-sizing: border-box; margin: 0; padding: 0; }
  html, body { width: 1200px; height: 711px; overflow: hidden; }
  body {
    background: var(--stage);
    font-family: "Roboto", Arial, sans-serif;
    color: var(--ink);
    position: relative;
  }
  .card {
    position: absolute;
    width: 540px;
    height: 309px;
    background: var(--card);
    border-radius: 3px;
    top: 201px;
    overflow: hidden;
  }
  .card--front { left: 40px; }
  .card--back { left: 620px; }

  .brand-name {
    font-family: "Roboto", Arial, sans-serif;
    font-weight: 700;
    color: var(--ink);
    text-transform: uppercase;
    letter-spacing: 0.04em;
    line-height: 1.15;
    text-align: center;
  }
  .card--front .brand-name {
    position: absolute;
    left: 60px; right: 60px; top: 92px;
    font-size: 30px;
  }
  .services {
    position: absolute;
    left: 30px; right: 30px; bottom: 44px;
    text-align: center;
  }
  .services__title {
    font-weight: 700;
    font-size: 11px;
    letter-spacing: 0.02em;
    margin-bottom: 4px;
  }
  .services__text { font-size: 11px; color: var(--ink-soft); }

  .card--back .brand-name {
    position: absolute;
    right: 28px; top: 32px;
    width: 280px;
    font-size: 21px;
    text-align: right;
  }
  .holder {
    position: absolute;
    left: 22px; bottom: 24px;
    writing-mode: vertical-rl;
    transform: rotate(180deg);
    white-space: nowrap;
    font-family: "Montserrat", Arial, sans-serif;
  }
  .holder__name { font-size: 25px; line-height: 1.05; }
  .holder__first { font-weight: 600; }
  .holder__last { font-weight: 300; }
  .holder__title { font-size: 12px; font-weight: 600; margin-left: 3px; }

  .contact {
    position: absolute;
    right: 26px; bottom: 28px;
    text-align: right;
    font-size: 11.5px;
    line-height: 1.55;
    color: var(--ink-soft);
  }
  .contact__address { margin-bottom: 10px; }
  .contact__row { display: flex; justify-content: flex-end; align-items: center; gap: 7px; }
  .contact__icon { width: 11px; height: 11px; fill: var(--ink); flex: none; }
</style>
</head>
<body>
  <section class="card card--front" aria-label="Card front">
    <p class="brand-name">Coastal Tundrabridge Advisory</p>
    <div class="services">
      <p class="services__title">OUR SERVICES</p>
      <p class="services__text">We provide specialized permafrost services to the mining, transportation, and oil &amp; gas industries</p>
    </div>
  </section>

  <section class="card card--back" aria-label="Card back">
    <p class="brand-name">Coastal Tundrabridge Advisory</p>
    <div class="holder">
      <p class="holder__name"><span class="holder__first">Matthias</span> <span class="holder__last">Korhonen</span></p>
      <p class="holder__title">PhD</p>
    </div>
    <div class="contact">
      <p class="contact__address">PO Box 418259<br>Quillwater, Alaska 99642</p>
      <p class="contact__row">+1-907-555-0143
        <svg class="contact__icon" viewBox="0 0 24 24" aria-hidden="true"><path d="M6.6 10.8a15.1 15.1 0 0 0 6.6 6.6l2.2-2.2c.3-.3.7-.4 1-.2 1.1.4 2.3.6 3.6.6.6 0 1 .4 1 1V20c0 .6-.4 1-1 1A17 17 0 0 1 3 4c0-.6.4-1 1-1h3.5c.6 0 1 .4 1 1 0 1.3.2 2.5.6 3.6.1.3 0 .7-.2 1z"/></svg>
      </p>
      <p class="contact__row">mkorhonen@tundrabridgeadvisory.example
        <svg class="contact__icon" viewBox="0 0 24 24" aria-hidden="true"><path d="M2 5h20v14H2zm2 2v.5l8 5 8-5V7zm0 2.8V17h16V9.8l-8 5z"/></svg>
      </p>
      <p class="contact__row">www.coastaltundrabridgeadvisory.example
        <svg class="contact__icon" viewBox="0 0 24 24" aria-hidden="true"><path d="M12 2a10 10 0 1 0 0 20 10 10 0 0 0 0-20zm6.9 6h-3a15 15 0 0 0-1.3-3.9A8 8 0 0 1 18.9 8zM12 4c.8 1.2 1.5 2.5 1.9 4h-3.8c.4-1.5 1.1-2.8 1.900-4zM4.3 14a8 8 0 0 1 0-4h3.4a16 16 0 0 0 0 4zm.8 2h3a15 15 0 0 0 1.3 3.9A8 8 0 0 1 5.1 16zm3-8h-3a8 8 0 0 1 4.3-3.9C8.8 5.3 8.4 6.6 8.1 8zM12 20c-.8-1.2-1.5-2.5-1.9-4h3.8c-.4 1.5-1.1 2.8-1.9 4zm2.3-6H9.7a14 14 0 0 1 0-4h4.6a14 14 0 0 1 0 4zm.3 5.9c.6-1.2 1-2.5 1.3-3.9h3a8 8 0 0 1-4.3 3.9zm1.7-5.9a16 16 0 0 0 0-4h3.4a8 8 0 0 1 0 4z"/></svg>
      </p>
    </div>
  </section>
</body>
</html>
```